BOLD & MINIMALIST DESIGN NEEDED

We want a very bold but minimalistic business card design that is impactful and utilizes both sides of the business card. Our current logo is included for your use.

We want bold fonts and good use of negative space. We don't want the logo to overpower the design.

Target Market(s)

Professionals who are building new commercial buildings.

Industry/Entity Type

Construction

Contact Information for Business Card

Name, Title, email, office phone, cell phone, website

Font styles to use
Serif
Sans Serif

Requirements
Must have
• Bold design!

```html
<!DOCTYPE html>
<html lang="en">
<head>
<meta charset="utf-8">
<title>Ridgeline Design + Build — Business Card</title>
<link href="https://fonts.googleapis.com/css2?family=Montserrat:wght@400;500;800&display=swap" rel="stylesheet">
<style>
  :root{
    --stage:#3a3a3a;
    --brand-green:#86c440;
    --brand-green-light:#9fd25f;
    --ink:#0c0c0c;
    --paper:#ffffff;
    --card-radius:22px;
  }
  *{box-sizing:border-box;margin:0;padding:0}
  html,body{width:1200px;height:689px;overflow:hidden}
  body{
    background:var(--stage);
    font-family:"Montserrat",Arial,sans-serif;
    display:flex;align-items:center;justify-content:center;gap:40px;
  }
  .card{
    position:relative;width:540px;height:310px;
    border-radius:var(--card-radius);overflow:hidden;
    box-shadow:0 18px 40px rgba(0,0,0,.45);
  }
  /* Front */
  .card--front{
    background:linear-gradient(120deg,var(--brand-green-light) 0%,var(--brand-green) 45%);
    display:flex;align-items:center;justify-content:center;
  }
  .wordmark{
    display:flex;align-items:center;gap:14px;
    color:var(--paper);font-weight:800;text-transform:uppercase;
  }
  .wordmark__square{width:26px;height:26px;background:var(--paper);flex:none}
  .wordmark__name{font-size:36px;letter-spacing:1px;line-height:1.1}
  /* Back */
  .card--back{background:var(--paper)}
  .swoosh{position:absolute;inset:0;width:100%;height:100%}
  .card--back .wordmark{
    position:absolute;left:30px;top:146px;color:var(--ink);gap:10px;
  }
  .card--back .wordmark__square{width:18px;height:18px;background:var(--ink)}
  .card--back .wordmark__name{font-size:18px}
  .contact{
    position:absolute;right:26px;top:78px;text-align:right;color:var(--paper);
  }
  .contact__name{
    color:var(--brand-green);font-weight:800;font-size:21px;letter-spacing:.5px;text-transform:uppercase;line-height:1.1;
  }
  .contact__title{font-size:11.5px;font-weight:500;letter-spacing:.5px;margin-top:3px}
  .contact__list{list-style:none;margin-top:24px;font-size:12px;line-height:1.75}
  .contact__list li{display:flex;align-items:center;justify-content:flex-end;gap:8px}
  .contact__icon{width:11px;height:11px;fill:var(--brand-green);flex:none}
</style>
</head>
<body>
  <section class="card card--front" aria-label="Card front">
    <div class="wordmark">
      <span class="wordmark__square"></span>
      <span class="wordmark__name">Ridgeline<br>Design + Build</span>
    </div>
  </section>

  <section class="card card--back" aria-label="Card back">
    <svg class="swoosh" viewBox="0 0 540 310" preserveAspectRatio="none" aria-hidden="true">
      <defs>
        <path id="wave" d="M490,0 C380,0 320,40 295,130 C265,230 200,295 90,310 L600,310 L600,0 Z"/>
      </defs>
      <use href="#wave" fill="var(--ink)" transform="translate(-30,0)"/>
      <use href="#wave" fill="var(--paper)" transform="translate(-25,0)"/>
      <use href="#wave" fill="var(--brand-green)" transform="translate(-18,0)"/>
      <use href="#wave" fill="var(--paper)" transform="translate(-7,0)"/>
      <use href="#wave" fill="var(--ink)"/>
    </svg>

    <div class="wordmark">
      <span class="wordmark__square"></span>
      <span class="wordmark__name">Ridgeline<br>Design + Build</span>
    </div>

    <div class="contact">
      <p class="contact__name">Marcus Vale</p>
      <p class="contact__title">OWNER-CEO</p>
      <ul class="contact__list">
        <li>123 456 789
          <svg class="contact__icon" viewBox="0 0 12 12"><path d="M2.5 1h2l1 3-1.5 1a7 7 0 0 0 3 3l1-1.5 3 1v2a1 1 0 0 1-1 1A10 10 0 0 1 1.5 2a1 1 0 0 1 1-1z"/></svg></li>
        <li>123 456 789
          <svg class="contact__icon" viewBox="0 0 12 12"><path d="M3.5 0h5a1 1 0 0 1 1 1v10a1 1 0 0 1-1 1h-5a1 1 0 0 1-1-1V1a1 1 0 0 1 1-1zm.5 1.5v8h4v-8z"/></svg></li>
        <li>info@ridgelinebuild.com
          <svg class="contact__icon" viewBox="0 0 12 12"><path d="M0 2h12v8H0zm1 1v.4l5 3.2 5-3.2V3z"/></svg></li>
        <li>www.ridgelinebuild.com
          <svg class="contact__icon" viewBox="0 0 12 12"><circle cx="6" cy="6" r="5.5"/></svg></li>
      </ul>
    </div>
  </section>
</body>
</html>
```